Modern/Bold/Unique Prenatal Vitamin label redesign

We are in need of a design update for our Prenatal Vitamin label. We want to modernize our label and give it a fresh feel.
It should bring a feeling of fun, joy, and sophistication, but also be bold/edgy/unique and portray Trust and Authority. Our buyers are mainly mothers in the age range of 25-34 who are pregnant or breastfeeding.
I will attach our current label design, as well as some inspiration to go off of.
We like the idea of having a clean, easy to read label label with bold/vibrant colors and fonts. We like the idea of having some retro vibes in it as well
Please see the attached artwork for design inspiration (New Design Idea). We like the idea of having a pregnant mother image like the attachment on the label, with the rest of the label being white. Please come up with a unique drawing/image for the design. We cannot use a copied image or stock image.
We look forward to working with you!

```html
<!DOCTYPE html>
<html lang="en">
<head>
<meta charset="utf-8">
<title>Bloom Nest Prenatal Glow+ Label</title>
<link href="https://fonts.googleapis.com/css2?family=Rubik:wght@300;400;500;700;900&display=swap" rel="stylesheet">
<style>
  :root {
    --backdrop: #b3b3b3;
    --label-top: #9d9ccb;
    --label-mid: #b3a2d2;
    --label-bottom: #c6a6d6;
    --sheen: rgba(235, 230, 245, 0.55);
    --halo: rgba(160, 130, 200, 0.45);
    --halo-ring: #8e6fc2;
    --ink-white: #f4f2f8;
    --ink-soft: #efe9f6;
    --title-stroke: #5b3fae;
    --title-glow: #c17ce8;
    --title-shadow: #8a6cc4;
    --capsule: #4a3a9c;
    --figure-teal: #6fc6c4;
    --figure-rose: #e06a86;
    --figure-skin: #f2cbb3;
  }
  * { box-sizing: border-box; margin: 0; padding: 0; }
  html, body { width: 1200px; height: 900px; overflow: hidden; }
  body {
    background: var(--backdrop);
    font-family: "Rubik", sans-serif;
    position: relative;
  }
  .label {
    position: absolute;
    left: 240px; top: 15px;
    width: 720px; height: 870px;
    overflow: hidden;
    background:
      linear-gradient(90deg, transparent 0%, transparent 55%, var(--sheen) 82%, transparent 100%),
      linear-gradient(180deg, var(--label-top) 0%, var(--label-mid) 50%, var(--label-bottom) 100%);
  }
  .brand {
    position: absolute;
    top: 42px; left: 0; width: 100%;
    display: flex; justify-content: center; align-items: center; gap: 14px;
    color: var(--ink-white);
    font-weight: 400; font-size: 50px; letter-spacing: 0.5px;
  }
  .brand-dot {
    width: 22px; height: 22px; border-radius: 50%;
    background: var(--ink-white);
  }
  .hero {
    position: absolute; left: 40px; top: 120px;
    width: 640px; height: 420px;
  }
  .title {
    position: absolute; left: 0; width: 100%;
    text-align: center;
    font-weight: 900; color: var(--ink-white);
    -webkit-text-stroke: 5px var(--title-stroke);
    paint-order: stroke fill;
    text-shadow: 0 0 0 var(--title-glow), 6px 8px 0 var(--title-shadow);
    line-height: 1;
  }
  .title-main { top: 478px; font-size: 112px; letter-spacing: -2px; }
  .title-sub { top: 576px; font-size: 108px; letter-spacing: -2px; padding-left: 20px; }
  .title-sub sup { font-size: 70px; vertical-align: 30px; }
  .tagline {
    position: absolute; top: 718px; left: 0; width: 100%;
    text-align: center; color: var(--ink-soft);
    font-size: 27px; line-height: 1.4;
  }
  .tagline-lead { font-weight: 300; display: block; }
  .tagline-focus { font-weight: 700; display: block; }
  .supplement {
    position: absolute; left: 66px; bottom: 44px;
    color: var(--ink-soft); font-weight: 300; font-size: 28px;
  }
  .count {
    position: absolute; right: 62px; bottom: 40px;
    display: flex; align-items: center; gap: 6px;
    color: var(--ink-white);
  }
  .count-number { font-weight: 700; font-size: 52px; line-height: 1; }
  .count-unit { font-weight: 500; font-size: 17px; line-height: 1.05; }
</style>
</head>
<body>
  <main class="label">
    <div class="brand"><span class="brand-dot"></span><span class="brand-name">Bloom Nest</span></div>

    <svg class="hero" viewBox="0 0 640 420" aria-hidden="false">
      <defs>
        <radialGradient id="haloFill" cx="50%" cy="50%" r="50%">
          <stop offset="0%" stop-color="#a58bd2" stop-opacity="0.55"/>
          <stop offset="100%" stop-color="#a58bd2" stop-opacity="0"/>
        </radialGradient>
        <linearGradient id="figureFill" x1="0" y1="0" x2="1" y2="1">
          <stop offset="0%" stop-color="#e06a86"/>
          <stop offset="45%" stop-color="#f2cbb3"/>
          <stop offset="100%" stop-color="#6fc6c4"/>
        </linearGradient>
      </defs>
      <circle cx="320" cy="240" r="300" fill="url(#haloFill)"/>
      <path d="M320 420 L150 260 C80 190 110 60 215 60 C265 60 300 90 320 125 C340 90 375 60 425 60 C530 60 560 190 490 260 Z"
            fill="#ececee" stroke="#8e6fc2" stroke-width="32" stroke-opacity="0.55"/>
      <rect x="220" y="10" width="210" height="410" rx="90" fill="url(#figureFill)"
            role="img" aria-label="Illustration of a pregnant mother cradling her belly"/>
    </svg>

    <div class="title title-main">PRENATAL</div>
    <div class="title title-sub">GLOW<sup>+</sup></div>

    <p class="tagline">
      <span class="tagline-lead">Once Daily Premium Multivitamin for</span>
      <span class="tagline-focus">Mama &amp; Baby *</span>
    </p>

    <div class="supplement">Dietary Supplement</div>

    <div class="count">
      <svg width="30" height="40" viewBox="0 0 30 40" aria-hidden="true">
        <g transform="rotate(30 15 20)">
          <rect x="7" y="2" width="16" height="36" rx="8" fill="#f4f2f8" stroke="var(--capsule)" stroke-width="2.5"/>
          <path d="M7 20 V10 a8 8 0 0 1 16 0 V20 Z" fill="var(--capsule)"/>
        </g>
      </svg>
      <span class="count-number">90</span>
      <span class="count-unit">VEGGIE<br>CAPSULES</span>
    </div>
  </main>
</body>
</html>
```